Fire Risk Assessment App needs a sleek UI design

I need a sleek, modern but professional design for my 5 page Fire Risk Assessment App. Include gradient background, fire themed colours including reds, yellows, light orange and a touch of black. Design must ooze simplicity and professionalism. This is for the UK market. See attached images and word doc for more information.

Target Market(s)

General public and business owners

Industry/Entity Type

Technology / Fire Safety

Colors
00AB8E
00BBA5
67D7C9
C6EFE9
E9F9F6
59FF00
82FF00
B8FF75
E3FFCB
F4FFEA
FFC000
F8CF3A
FAE287
FDF2CF
FEFAEE
F0912C
F2A743
F7CA91
FBE8D2
FDF5EE
EE7325
F08F49
F5BC92
FAE3D3
FDF4ED
EB3D1F
EC4F4E
F09395
F8D3D4
FCEDEE

```html
<!DOCTYPE html>
<html lang="en">
<head>
<meta charset="utf-8">
<title>Fire Risk Assessment App – Screens</title>
<link href="https://fonts.googleapis.com/css2?family=Roboto:wght@400;500;700&display=swap" rel="stylesheet">
<style>
:root{
  --stage:#808080;
  --peach-top:#F8CC94;
  --peach-bottom:#FBBF7C;
  --white:#FFFFFF;
  --ink:#1E1E1E;
  --red:#EB1F1F;
  --green:#3BC43B;
  --orange-line:#E98A3A;
  --icon-fill:#F3B06A;
}
*{box-sizing:border-box;margin:0;padding:0}
html,body{width:1200px;height:724px;overflow:hidden}
body{background:var(--stage);font-family:'Roboto',Arial,sans-serif;position:relative}
.screen{position:absolute;top:76px;width:262px;height:570px;border-radius:26px;overflow:hidden;
  background:linear-gradient(180deg,var(--peach-top),var(--peach-bottom))}
.screen-welcome{left:105px}
.screen-dashboard{left:471px}
.screen-support{left:837px}
.abs{position:absolute}
.white-text{color:var(--white);font-weight:700}

/* welcome */
.tagline{left:0;right:0;top:40px;text-align:center;font-size:10.5px;line-height:15px}
.form-preview{left:62px;top:81px;width:134px;height:144px;border-radius:4px;
  background:linear-gradient(180deg,#FFFFFF,#FCE6CC)}
.voice-pill{left:23px;top:244px;width:214px;height:23px;border:1px solid rgba(255,255,255,.8);border-radius:12px;
  font-size:6.5px;color:var(--white);padding-left:14px;line-height:21px}
.mic-dot{position:absolute;right:3px;top:3px;width:15px;height:15px;border-radius:50%;background:var(--white)}
.mic-dot svg{position:absolute;left:4px;top:3px}
.action-pill{left:23px;width:214px;height:50px;border-radius:25px;background:var(--white);
  text-align:center;font-size:8.5px;font-weight:700;color:var(--ink);padding-top:30px}
.avatar-badge{width:46px;height:46px;border-radius:50%;background:var(--white);left:107px}
.avatar-badge span{position:absolute;left:4px;top:4px;width:38px;height:38px;border-radius:50%;background:var(--icon-fill)}
.avatar-badge svg{position:absolute;left:12px;top:11px}
.note{left:0;right:0;text-align:center;font-size:9px;line-height:13px}

/* headers */
.header-icon{left:20px;top:25px;width:30px;height:30px;border-radius:50%;background:rgba(255,255,255,.25)}
.header-icon svg{position:absolute;left:7px;top:7px}
.screen-title{left:0;right:0;top:30px;text-align:center;font-size:15px}

/* dashboard */
.start-button{left:100px;top:73px;width:60px;height:60px;border-radius:50%;background:var(--red)}
.start-button svg{position:absolute;left:20px;top:20px}
.option-circle{width:44px;height:44px;border-radius:50%;background:var(--white);box-shadow:0 1px 3px rgba(0,0,0,.12)}
.option-circle span{position:absolute;left:10px;top:10px;width:24px;height:24px;border-radius:4px}
.option-label{font-size:6.5px;line-height:7px;color:var(--white);font-weight:700;text-align:center}
.section-bar{left:23px;width:214px;height:24px;background:var(--white);border-radius:2px;
  font-size:9px;font-weight:700;color:var(--ink);padding-left:9px;line-height:24px}
.section-bar svg{position:absolute;right:7px;top:4px}
.list-item{left:34px;font-size:8.5px;font-weight:700;color:var(--white);line-height:11px;padding-left:14px}
.list-item::before{content:"";position:absolute;left:0;top:2px;width:5px;height:5px;border:1.5px solid var(--white);border-radius:50%}
.venue-badge{left:24px;top:245px;width:33px;height:33px;border-radius:50%;background:var(--white)}
.venue-badge svg{position:absolute;left:9px;top:9px}
.venue-name{left:64px;top:256px;font-size:9px}

/* nav */
.tab-bar{left:9px;top:532px;width:244px;height:38px;background:var(--white);border-radius:8px 8px 0 0}
.tab{position:absolute;top:9px;width:18px;height:18px}
.tab.active::after{content:"";position:absolute;left:-5px;top:25px;width:27px;height:3px;border-radius:2px;background:var(--red)}

/* support */
.field-label{left:21px;top:78px;font-size:6.5px;color:var(--white)}
.field-mic{left:227px;top:77px}
.message-box{left:23px;top:93px;width:214px;height:102px;background:var(--white);border-radius:2px}
.send-button{left:179px;top:200px;width:57px;height:23px;background:var(--red);border-radius:2px;
  color:var(--white);font-size:7px;font-weight:700;text-align:center;line-height:23px}
</style>
</head>
<body>

<!-- Welcome -->
<section class="screen screen-welcome">
  <h1 class="abs tagline white-text">The Most User Friendly<br>Fire Risk Assessment App Available.</h1>
  <div class="abs form-preview" role="img" aria-label="Preview of a fire risk assessment form page"></div>
  <div class="abs voice-pill">Quick tab responses and voice activated typing
    <span class="mic-dot"><svg width="7" height="9" viewBox="0 0 7 9"><rect x="2" y="0" width="3" height="5" rx="1.5" fill="#555"/><path d="M1 4a2.5 2.5 0 0 0 5 0M3.5 7v2" stroke="#555" fill="none" stroke-width=".8"/></svg></span>
  </div>

  <div class="abs action-pill" style="top:308px">Create A Free Account</div>
  <div class="abs avatar-badge" style="top:286px"><span></span>
    <svg width="22" height="22" viewBox="0 0 22 22"><circle cx="9" cy="6" r="4" fill="#fff"/><path d="M2 19c0-5 3-7 7-7s7 2 7 7z" fill="#fff"/><path d="M17 12v7M13.5 15.5h7" stroke="#fff" stroke-width="2"/></svg>
  </div>
  <p class="abs note white-text" style="top:374px">Any Responsible Person Can Do It.</p>

  <div class="abs action-pill" style="top:424px">Customer Login</div>
  <div class="abs avatar-badge" style="top:402px"><span></span>
    <svg width="22" height="22" viewBox="0 0 22 22"><circle cx="9" cy="6" r="4" fill="#fff"/><path d="M2 19c0-5 3-7 7-7s7 2 7 7z" fill="#fff"/><rect x="13" y="14" width="7" height="6" rx="1" fill="#fff"/><path d="M14.5 14v-2a2 2 0 0 1 4 0v2" stroke="#fff" fill="none" stroke-width="1.4"/></svg>
  </div>
  <p class="abs note white-text" style="top:494px">Created and endorsed by<br>Veteran Fire Officers</p>
</section>

<!-- Dashboard -->
<section class="screen screen-dashboard">
  <div class="abs header-icon"><svg width="16" height="16" viewBox="0 0 16 16" fill="none" stroke="#fff" stroke-width="1.3"><path d="M2 12a6 6 0 1 1 12 0"/><path d="M8 11l3-4"/></svg></div>
  <h1 class="abs screen-title white-text">Dashboard</h1>

  <div class="abs start-button"><svg width="20" height="20" viewBox="0 0 20 20"><path d="M10 2v16M2 10h16" stroke="#fff" stroke-width="4"/></svg></div>
  <span class="abs option-label" style="left:84px;top:134px">Start</span>
  <span class="abs option-label" style="left:158px;top:127px">Fire Risk<br>Assessment</span>
  <div class="abs option-circle" style="left:71px;top:146px"><span role="img" aria-label="House icon for residential assessment" style="background:#C8553F"></span></div>
  <div class="abs option-circle" style="left:145px;top:146px"><span role="img" aria-label="Office building icon for commercial assessment" style="background:#4A7BC8"></span></div>

  <div class="abs section-bar" style="top:213px">Complete
    <svg width="16" height="16" viewBox="0 0 16 16" fill="none" stroke="var(--green)" stroke-width="1.6"><circle cx="8" cy="8" r="6.5"/><path d="M4.5 8l2.5 2.5 5-5.5"/></svg>
  </div>
  <div class="abs venue-badge"><svg width="15" height="15" viewBox="0 0 15 15" fill="none" stroke="var(--orange-line)" stroke-width="1"><rect x="1" y="3" width="13" height="11"/><path d="M1 6h13M4 8h3v6M9 8h3v3H9z"/></svg></div>
  <p class="abs venue-name white-text">Leo's Barbershop</p>

  <div class="abs section-bar" style="top:312px">In Progress
    <svg width="16" height="16" viewBox="0 0 16 16" fill="none" stroke="var(--orange-line)" stroke-width="1.4"><path d="M13.5 8A5.5 5.5 0 0 1 3 10.5M2.5 8A5.5 5.5 0 0 1 13 5.5"/><path d="M13 2.5v3h-3M3 13.5v-3h3"/></svg>
  </div>
  <p class="abs list-item" style="top:349px">Elm Road School</p>
  <p class="abs list-item" style="top:366px">Oakfield Nursing Home</p>

  <div class="abs section-bar" style="top:411px">Purchases
    <svg width="16" height="16" viewBox="0 0 16 16" fill="none" stroke="var(--ink)" stroke-width="1.1"><path d="M2.5 5h11l-1 10h-9z"/><path d="M5.5 5V3.5a2.5 2.5 0 0 1 5 0V5"/></svg>
  </div>
  <p class="abs list-item" style="top:448px">Residential Fire Risk Assessment</p>
  <p class="abs list-item" style="top:466px">Commercial Fire Risk Assessment</p>
  <p class="abs list-item" style="top:484px">Commercial Fire Risk Assessment</p>

  <nav class="abs tab-bar">
    <svg class="tab active" style="left:17px" viewBox="0 0 18 18" fill="none" stroke="var(--orange-line)" stroke-width="1.3"><path d="M2 14a7 7 0 1 1 14 0"/><path d="M9 13l3.5-5"/></svg>
    <svg class="tab" style="left:80px" viewBox="0 0 18 18" fill="none" stroke="var(--orange-line)" stroke-width="1.3"><rect x="1.5" y="5" width="15" height="10" rx="1"/><path d="M1.5 8.5h15M3.5 3h11"/></svg>
    <svg class="tab" style="left:143px" viewBox="0 0 18 18" fill="none" stroke="var(--orange-line)" stroke-width="1.3"><path d="M2 3h14v10H7l-4 3v-3H2z"/><path d="M5 6.5h8M5 9.5h6"/></svg>
    <svg class="tab" style="left:206px" viewBox="0 0 18 18" fill="none" stroke="var(--orange-line)" stroke-width="1.3"><path d="M7 2H3v14h4M11 5l4 4-4 4M15 9H6"/></svg>
  </nav>
</section>

<!-- Technical Support -->
<section class="screen screen-support">
  <div class="abs header-icon"><svg width="16" height="16" viewBox="0 0 16 16" fill="none" stroke="#fff" stroke-width="1.2"><path d="M2 3h12v8H6l-3 3v-3H2z"/><path d="M5 6h6M5 8.5h5"/></svg></div>
  <h1 class="abs screen-title white-text">Technical Support</h1>

  <p class="abs field-label">Type / Record your response here</p>
  <svg class="abs field-mic" width="7" height="9" viewBox="0 0 7 9"><rect x="2" y="0" width="3" height="5" rx="1.5" fill="#fff"/><path d="M1 4a2.5 2.5 0 0 0 5 0M3.5 7v2" stroke="#fff" fill="none" stroke-width=".8"/></svg>
  <div class="abs message-box"></div>
  <div class="abs send-button">SEND</div>

  <nav class="abs tab-bar">
    <svg class="tab" style="left:17px" viewBox="0 0 18 18" fill="none" stroke="var(--orange-line)" stroke-width="1.3"><path d="M2 14a7 7 0 1 1 14 0"/><path d="M9 13l3.5-5"/></svg>
    <svg class="tab" style="left:80px" viewBox="0 0 18 18" fill="none" stroke="var(--orange-line)" stroke-width="1.3"><rect x="1.5" y="5" width="15" height="10" rx="1"/><path d="M1.5 8.5h15M3.5 3h11"/></svg>
    <svg class="tab active" style="left:143px" viewBox="0 0 18 18" fill="none" stroke="var(--orange-line)" stroke-width="1.3"><path d="M2 3h14v10H7l-4 3v-3H2z"/><path d="M5 6.5h8M5 9.5h6"/></svg>
    <svg class="tab" style="left:206px" viewBox="0 0 18 18" fill="none" stroke="var(--orange-line)" stroke-width="1.3"><path d="M7 2H3v14h4M11 5l4 4-4 4M15 9H6"/></svg>
  </nav>
</section>

</body>
</html>
```